Emergency and Referral Vet Hospital promotional sticker design

We're looking at getting some stickers designed that we could give to clients to put on their cars for promotion and advertising. If they could also be suitable for a goodie bag for conference too that would be great. I like the look of water-colour backgrounds, we'll need to include our logo and probably our address (Unit 3/215 Korrinup Road Tallowmere). We also have a hospital motto "... because they're family" if that could somehow be integrated, we only care for small animals (dogs, cats etc) but the design is very open to suggestion. Would love to see what you can create.

Industry/Entity Type

Veterinary

Colors
0054AA
0677BA
7BADD7
CADEEF
E8F1F8
0094D4
00A9DD
6FCCEA
C7EBF8
E9F6FB

Requirements
Nice to have
• Think beach vibes, blues maybe paw print shapes etc

```html
<!DOCTYPE html>
<html lang="en">
<head>
<meta charset="utf-8">
<title>Tidewell – Because they're Family stickers</title>
<link href="https://fonts.googleapis.com/css2?family=Pacifico&family=Great+Vibes&family=Roboto:wght@400;500;700&display=swap" rel="stylesheet">
<style>
  :root {
    --page: #c4c4c4;
    --navy: #0b4fae;
    --navy-deep: #0054aa;
    --sky: #1e9ad8;
    --cyan: #00a9dd;
    --cyan-light: #6fccea;
    --mist: #e9f6fb;
    --pale: #c7ebf8;
    --white: #ffffff;
    --ink: #111827;
    --script-blue: #1c8fcf;
  }
  * { margin: 0; padding: 0; box-sizing: border-box; }
  html, body { width: 945px; height: 1200px; overflow: hidden; }
  body { background: var(--page); font-family: "Roboto", sans-serif; position: relative; }

  .sticker { position: absolute; left: 118px; width: 709px; height: 473px; overflow: hidden; }
  .sticker--family { top: 110px; background: var(--navy); }
  .sticker--trio { top: 619px; background: var(--sky); }

  .shape { position: absolute; left: 0; top: 0; }

  .photo { position: absolute; }
  .photo--pack { left: 0; top: 0; width: 300px; height: 250px;
    background: radial-gradient(ellipse at 55% 55%, #b7825a 0%, #d9c3a8 40%, #f2f0ee 75%); }
  .photo--pair { left: 345px; top: 300px; width: 364px; height: 173px;
    background: radial-gradient(ellipse at 35% 45%, #9c4a1c 0%, #c36a2c 35%, rgba(231,160,90,0.6) 65%, rgba(255,255,255,0) 85%); }

  .headline-script { position: absolute; left: 355px; top: 44px; font-family: "Pacifico", cursive;
    font-size: 34px; color: var(--white); letter-spacing: 0.5px; }
  .headline-big { position: absolute; left: 350px; top: 88px; font-family: "Roboto", sans-serif;
    font-weight: 500; font-size: 104px; line-height: 1; color: var(--white); }

  .brand { position: absolute; display: flex; align-items: center; gap: 8px; white-space: nowrap; }
  .brand__dot { width: 22px; height: 22px; border-radius: 50%; flex: none; }
  .brand__name { font-family: "Roboto", sans-serif; font-weight: 500; font-size: 26px; line-height: 1; }
  .sticker--family .brand { left: 96px; top: 300px; }
  .sticker--family .brand__dot { background: var(--cyan-light); }
  .sticker--family .brand__name { color: var(--white); }

  .location-tag { position: absolute; left: 0; top: 391px; width: 212px; height: 26px;
    background: var(--cyan); border-radius: 0 13px 13px 0; display: flex; align-items: center;
    padding-left: 30px; gap: 10px; color: var(--white); font-size: 14px; font-weight: 500; letter-spacing: 0.5px; }
  .address { position: absolute; color: var(--white); font-size: 17px; white-space: nowrap; }
  .sticker--family .address { left: 30px; top: 425px; }

  .photo--cat { left: 132px; top: 16px; width: 140px; height: 306px;
    background: linear-gradient(180deg, #8a8580 0%, #6b665f 55%, #5a554f 100%); border-radius: 70px 70px 10px 10px; }
  .photo--collie { left: 284px; top: 10px; width: 186px; height: 312px;
    background: linear-gradient(180deg, #2a2522 0%, #3b3430 45%, #c49a6c 75%, #f1ece6 100%); border-radius: 90px 90px 10px 10px; }
  .photo--pup { left: 480px; top: 14px; width: 140px; height: 308px;
    background: linear-gradient(180deg, #c9b8a6 0%, #e9e2da 55%, #f4f1ed 100%); border-radius: 70px 70px 10px 10px; }

  .corner-badge { position: absolute; left: -82px; top: -82px; width: 200px; height: 200px;
    border-radius: 50%; background: var(--white); }
  .sticker--trio .brand { left: 12px; top: 56px; gap: 6px; }
  .sticker--trio .brand__dot { background: var(--navy-deep); width: 12px; height: 12px; }
  .sticker--trio .brand__name { color: var(--navy-deep); font-size: 18px; }

  .tagline-script { position: absolute; left: 0; right: 0; top: 326px; text-align: center;
    font-family: "Great Vibes", cursive; font-size: 66px; color: var(--script-blue); }
  .sticker--trio .address { left: 0; right: 0; top: 416px; display: flex; justify-content: center;
    align-items: center; gap: 8px; color: var(--ink); font-weight: 500; font-size: 21px; }
</style>
</head>
<body>

<section class="sticker sticker--family">
  <svg class="shape" width="709" height="473" viewBox="0 0 709 473">
    <path d="M0 0 H340 C330 60 320 100 345 150 C365 195 330 265 250 262 C190 260 170 300 110 292 C60 285 20 300 0 292 Z" fill="#00a9dd"/>
    <path d="M0 0 H325 C316 60 305 105 328 150 C345 190 310 248 245 246 C185 244 165 285 110 276 C60 268 20 284 0 276 Z" fill="#ffffff"/>
    <path d="M400 473 C405 420 420 375 470 355 C540 330 560 305 620 300 C670 296 690 290 709 285 V473 Z" fill="#00a9dd"/>
    <path d="M415 473 C420 425 435 388 482 370 C548 345 570 322 625 316 C670 312 692 305 709 300 V473 Z" fill="#ffffff"/>
  </svg>
  <div class="photo photo--pack" role="img" aria-label="Group photo of six dogs sitting together"></div>
  <div class="photo photo--pair" role="img" aria-label="Photo of a red retriever lying beside a ginger cat"></div>

  <p class="headline-script">Because they're</p>
  <h1 class="headline-big">Family</h1>

  <div class="brand"><span class="brand__dot"></span><span class="brand__name">Tidewell</span></div>

  <div class="location-tag">
    <svg width="12" height="16" viewBox="0 0 12 16"><path d="M6 0C2.7 0 0 2.6 0 5.9 0 10.3 6 16 6 16s6-5.7 6-10.1C12 2.6 9.3 0 6 0zm0 8.2A2.3 2.3 0 1 1 6 3.6a2.3 2.3 0 0 1 0 4.6z" fill="#ffffff"/></svg>
    LOCATION
  </div>
  <p class="address">Unit 3/215 Korrinup Road Tallowmere</p>
</section>

<section class="sticker sticker--trio">
  <svg class="shape" width="709" height="473" viewBox="0 0 709 473">
    <ellipse cx="355" cy="560" rx="420" ry="390" fill="#e9f6fb"/>
  </svg>
  <div class="photo photo--cat" role="img" aria-label="Photo of a tabby cat sitting"></div>
  <div class="photo photo--collie" role="img" aria-label="Photo of a tricolour shepherd dog sitting"></div>
  <div class="photo photo--pup" role="img" aria-label="Photo of a pale cream dog sitting"></div>

  <div class="corner-badge"></div>
  <div class="brand"><span class="brand__dot"></span><span class="brand__name">Tidewell</span></div>

  <p class="tagline-script">Because they're Family</p>
  <p class="address">
    <svg width="14" height="19" viewBox="0 0 12 16"><path d="M6 0C2.7 0 0 2.6 0 5.9 0 10.3 6 16 6 16s6-5.7 6-10.1C12 2.6 9.3 0 6 0zm0 8.2A2.3 2.3 0 1 1 6 3.6a2.3 2.3 0 0 1 0 4.6z" fill="#1c8fcf"/></svg>
    Unit 3/215 Korrinup Road Tallowmere
  </p>
</section>

</body>
</html>
```